Birch Harbor - Countertop fabricator
Need stationary, business card and T-shirt design
Birch Harbor - Countertop fabricator -
Creative Brief
Simple
Karen Ousley
4 Wexford Lane Syracuse, NY13052
info@birchharborny.example
www.birchharborny.example
Back of card to list materials; Granite Quatz Marble Soapstone Solid Surface

```html
<!DOCTYPE html>
<html lang="en">
<head>
<meta charset="utf-8">
<title>Birch Harbor Stationery</title>
<link href="https://fonts.googleapis.com/css2?family=Tinos:wght@400;700&display=swap" rel="stylesheet">
<style>
:root{
  --bg:#ececec;
  --frame:#c9c9c9;
  --paper:#ffffff;
  --brown-dark:#4a3016;
  --brown:#6e4c26;
  --gold:#a8804a;
  --ink:#5a4a3a;
  --window:#e4e4e4;
}
*{margin:0;padding:0;box-sizing:border-box}
html,body{width:1200px;height:852px;overflow:hidden;background:var(--bg)}
body{font-family:"Tinos",serif;color:var(--ink)}
.canvas{position:relative;width:1200px;height:852px;border:3px solid var(--frame);overflow:hidden}
.sheet{position:absolute;background:var(--paper);box-shadow:0 1px 4px rgba(0,0,0,.18)}
.stripes{position:absolute;top:0;display:flex;gap:5px}
.stripes span{display:block;height:100%;background:linear-gradient(90deg,var(--brown),var(--gold) 60%,var(--brown))}
.mark{display:block;background:linear-gradient(135deg,var(--gold),var(--brown))}
.brand{position:absolute;font-family:"Tinos",serif;font-weight:400;color:var(--brown-dark);white-space:nowrap}
.contact{position:absolute;text-align:right;color:var(--ink);line-height:1.45;white-space:nowrap}

/* letterhead */
.letterhead{left:33px;top:40px;width:552px;height:761px}
.letterhead .stripes{left:10px;height:705px}
.letterhead .mark{position:absolute;left:135px;top:8px;width:40px;height:40px}
.letterhead .brand{left:104px;top:78px;font-size:26px}
.letterhead .contact{right:24px;bottom:12px;font-size:11px}

/* business card front */
.card-front{left:604px;top:38px;width:228px;height:139px}
.card-front .stripes{left:5px;height:139px;gap:3px}
.card-front .mark{position:absolute;left:67px;top:8px;width:26px;height:26px}
.card-front .brand{left:99px;top:14px;font-size:12px}
.card-front .person{position:absolute;left:41px;top:46px;font-size:12px;color:var(--brown)}
.card-front .contact{right:8px;top:102px;font-size:6.5px}

/* business card back */
.card-back{left:851px;top:131px;width:238px;height:130px;background:radial-gradient(ellipse at 45% 40%,var(--gold),var(--brown) 55%,var(--brown-dark))}
.card-back .mark{position:absolute;left:111px;top:24px;width:28px;height:28px;background:rgba(255,255,255,.35)}
.card-back .brand{left:0;right:0;top:62px;text-align:center;font-size:15px;color:#fff}
.card-back .materials{position:absolute;left:0;right:0;top:86px;text-align:center;font-size:7px;color:#f3e6d3;letter-spacing:.2px}

/* envelope front */
.envelope{left:604px;top:268px;width:588px;height:262px}
.envelope .stripes{left:6px;height:190px;gap:4px}
.envelope .mark{position:absolute;left:138px;top:24px;width:32px;height:32px}
.envelope .brand{left:90px;top:64px;font-size:20px}
.envelope .window{position:absolute;left:92px;top:157px;width:211px;height:45px;border-radius:9px;background:var(--window)}
.envelope .contact{right:10px;top:220px;font-size:7px}

/* envelope back */
.envelope-back{left:604px;top:544px;width:588px;height:106px}
.envelope-back svg{position:absolute;left:0;top:0}
.envelope-back .mark{position:absolute;left:290px;top:16px;width:28px;height:28px;background:rgba(255,255,255,.35)}
</style>
</head>
<body>
<main class="canvas">

  <section class="sheet letterhead" aria-label="Letterhead">
    <div class="stripes"><span style="width:16px"></span><span style="width:9px"></span><span style="width:8px"></span><span style="width:6px"></span><span style="width:4px"></span></div>
    <span class="mark"></span>
    <div class="brand">Birch Harbor</div>
    <div class="contact">
      4 Wexford Lane Syracuse, NY13052<br>
      Phone : 315-555-0142 | Cell : 315-555-0187 | Fax : 607-555-0163<br>
      Email : info@birchharborny.example &nbsp; www.birchharborny.example
    </div>
  </section>

  <section class="sheet card-front" aria-label="Business card front">
    <div class="stripes"><span style="width:7px"></span><span style="width:4px"></span><span style="width:3px"></span><span style="width:2px"></span></div>
    <span class="mark"></span>
    <div class="brand">Birch Harbor</div>
    <div class="person">Karen Ousley</div>
    <div class="contact">
      4 Wexford Lane Syracuse, NY13052<br>
      Phone : 315-555-0142 | Cell : 315-555-0187 | Fax : 607-555-0163<br>
      Email : info@birchharborny.example | www.birchharborny.example
    </div>
  </section>

  <section class="sheet card-back" aria-label="Business card back">
    <span class="mark"></span>
    <div class="brand">Birch Harbor</div>
    <div class="materials">Granite | Quartz | Marble | Soapstone | Solid Surface</div>
  </section>

  <section class="sheet envelope" aria-label="Envelope front">
    <div class="stripes"><span style="width:12px"></span><span style="width:7px"></span><span style="width:6px"></span><span style="width:5px"></span><span style="width:3px"></span></div>
    <span class="mark"></span>
    <div class="brand">Birch Harbor</div>
    <div class="window"></div>
    <div class="contact">
      4 Wexford Lane Syracuse, NY13052<br>
      Phone : 315-555-0142 | Cell : 315-555-0187 | Fax : 607-555-0163<br>
      Email : info@birchharborny.example | www.birchharborny.example
    </div>
  </section>

  <section class="sheet envelope-back" aria-label="Envelope back">
    <svg width="588" height="106" viewBox="0 0 588 106">
      <defs>
        <linearGradient id="flapFill" x1="0" y1="0" x2="1" y2="0">
          <stop offset="0" stop-color="#4a3016"/>
          <stop offset=".5" stop-color="#7a5630"/>
          <stop offset="1" stop-color="#4a3016"/>
        </linearGradient>
      </defs>
      <path d="M0 0 H588 V22 C470 24 380 30 304 58 C228 30 120 24 0 22 Z" fill="url(#flapFill)"/>
      <path d="M0 22 C120 24 228 30 304 58 C380 30 470 24 588 22" fill="none" stroke="#d6c7b3" stroke-width="1"/>
    </svg>
    <span class="mark"></span>
  </section>

</main>
</body>
</html>
```